SaaS Early tech startup business card design

Unique design for experience ecommerce platform company. the business cards will be used by executive members. conformance with color code is required.

```html
<!DOCTYPE html>
<html lang="en">
<head>
<meta charset="UTF-8">
<title>Velto business card</title>
<link href="https://fonts.googleapis.com/css2?family=Montserrat:wght@300;600&family=Roboto:wght@400&display=swap" rel="stylesheet">
<style>
  :root {
    --backdrop: #6b6767;
    --card-navy: #1f2137;
    --mark-grey: #9c9ca2;
    --ink-light: #f2f2f4;
    --accent-teal: #1b9a90;
  }
  * { margin: 0; padding: 0; box-sizing: border-box; }
  html, body { width: 1200px; height: 1200px; overflow: hidden; }
  body {
    background: var(--backdrop);
    position: relative;
    font-family: "Roboto", Arial, sans-serif;
  }
  .card {
    position: absolute;
    width: 594px;
    height: 349px;
    border-radius: 22px;
    background: var(--card-navy);
  }
  .card--front { left: 298px; top: 198px; }
  .card--back { left: 292px; top: 636px; }

  .brand-name {
    position: absolute;
    left: 0; right: 0;
    top: 80px;
    text-align: center;
    font-family: "Montserrat", Arial, sans-serif;
    font-weight: 600;
    font-size: 148px;
    line-height: 1;
    letter-spacing: -2px;
    color: var(--mark-grey);
  }
  .tagline {
    position: absolute;
    left: 0; right: 0;
    top: 245px;
    padding-left: 0.45em;
    text-align: center;
    font-family: "Montserrat", Arial, sans-serif;
    font-weight: 300;
    font-size: 15px;
    letter-spacing: 0.45em;
    color: var(--ink-light);
  }

  .holder {
    position: absolute;
    left: 132px;
    top: 141px;
    width: 160px;
    text-align: center;
  }
  .holder__name {
    font-family: "Montserrat", Arial, sans-serif;
    font-weight: 600;
    font-size: 22px;
    line-height: 1;
    letter-spacing: -0.5px;
    color: var(--accent-teal);
  }
  .holder__role {
    margin-top: 5px;
    font-size: 15px;
    color: var(--ink-light);
  }
  .contacts {
    position: absolute;
    left: 306px;
    top: 128px;
    list-style: none;
  }
  .contacts li {
    display: flex;
    align-items: center;
    height: 22px;
    font-size: 15px;
    color: var(--ink-light);
  }
  .contacts svg {
    width: 14px;
    height: 14px;
    margin-right: 17px;
    flex: none;
  }
  .address {
    position: absolute;
    left: 0; right: 0;
    top: 237px;
    padding-left: 16px;
    text-align: center;
    font-size: 15px;
    color: var(--ink-light);
  }
</style>
</head>
<body>
  <section class="card card--front">
    <div class="brand-name">velto</div>
    <div class="tagline">BUILT FOR YOU</div>
  </section>

  <section class="card card--back">
    <div class="holder">
      <div class="holder__name">Rami K.</div>
      <div class="holder__role">CTO/Owner</div>
    </div>
    <ul class="contacts">
      <li>
        <svg viewBox="0 0 14 14" aria-hidden="true"><path fill="var(--accent-teal)" d="M1 5c0-2 3-3 6-3s6 1 6 3v1h-3V4.5H4V6H1z M3 7h8l1 5H2z"/></svg>
        (09) 4826 VELT
      </li>
      <li>
        <svg viewBox="0 0 14 14" aria-hidden="true"><rect x="1" y="3" width="12" height="8" fill="var(--accent-teal)"/><path d="M1 3l6 5 6-5" fill="none" stroke="var(--card-navy)" stroke-width="1"/></svg>
        info@velto.net
      </li>
      <li>
        <svg viewBox="0 0 14 14" aria-hidden="true"><circle cx="7" cy="7" r="5.5" fill="var(--accent-teal)"/><path d="M1.5 7h11M7 1.5v11M7 1.5c-3 3-3 8 0 11M7 1.5c3 3 3 8 0 11" fill="none" stroke="var(--card-navy)" stroke-width="0.7"/></svg>
        www.velto.net
      </li>
    </ul>
    <div class="address">Meridian Tower, Tech Park District, UAE</div>
  </section>
</body>
</html>
```